Brightfield Ventures Inc. Letterhead

Creation of attractive and eye catching letterhead for a business start-up for the construction industry. Letterhead must relate to construction, but avoid standard hammer and tools in the design.

I forgot to add some details, sorry about that. Some pertinent info: Ph: 916-555-0187 brightfieldventures.example 448 Willowmere Ave, Ste 210 Folsom, CA 95999 info@brightfieldventures.example not sure if slogan should be in there" “Connecting construction professionals to create a purpose driven industry.” must be able to be used in word. Thanks!

```html
<!DOCTYPE html>
<html lang="en">
<head>
<meta charset="utf-8">
<title>Brightfield Ventures Inc. Letterhead</title>
<link rel="stylesheet" href="https://fonts.googleapis.com/css2?family=Lato:wght@400;700&family=Yellowtail&display=swap">
<style>
  :root {
    --navy: #1b2259;
    --red: #c11f2a;
    --body-text: #55565a;
    --paper: #ffffff;
  }
  html, body {
    margin: 0;
    padding: 0;
    overflow: hidden;
    background: var(--paper);
  }
  .letterhead {
    position: relative;
    width: 908px;
    height: 1200px;
    background: var(--paper);
    font-family: "Lato", sans-serif;
    overflow: hidden;
  }
  .brand {
    position: absolute;
    top: 92px;
    left: 0;
    width: 100%;
    display: flex;
    justify-content: center;
    align-items: center;
    gap: 12px;
  }
  .brand-mark {
    width: 20px;
    height: 20px;
    background: var(--red);
  }
  .brand-name {
    font-size: 26px;
    font-weight: 700;
    color: var(--navy);
    letter-spacing: 0.5px;
  }
  .letter {
    position: absolute;
    top: 316px;
    left: 74px;
    width: 752px;
  }
  .salutation {
    margin: 0 0 22px;
    font-size: 17px;
    font-weight: 700;
    color: var(--navy);
  }
  .letter-body p {
    margin: 0 0 20px;
    font-size: 16.6px;
    line-height: 27.4px;
    color: var(--body-text);
    text-align: justify;
    hyphens: auto;
  }
  .closing {
    margin: 36px 0 0;
    font-size: 19px;
    color: #2a2a2e;
  }
  .signature {
    margin: 2px 0 0;
    font-family: "Yellowtail", cursive;
    font-size: 38px;
    color: var(--navy);
  }
  .footer-wave {
    position: absolute;
    left: 0;
    top: 1030px;
    width: 908px;
    height: 170px;
    display: block;
  }
  .footer-contact {
    position: absolute;
    left: 0;
    top: 1136px;
    width: 100%;
    color: #ffffff;
    font-size: 13px;
    text-align: center;
    line-height: 24px;
  }
  .contact-line {
    display: flex;
    justify-content: center;
    align-items: center;
    gap: 14px;
  }
  .contact-item {
    display: inline-flex;
    align-items: center;
    gap: 5px;
  }
  .contact-icon {
    width: 11px;
    height: 11px;
    fill: #ffffff;
  }
</style>
</head>
<body>
<main class="letterhead">
  <header class="brand">
    <span class="brand-mark"></span>
    <span class="brand-name">Brightfield Ventures Inc.</span>
  </header>

  <section class="letter">
    <p class="salutation">Dear Mr. Lorem,</p>
    <div class="letter-body">
      <p>Lorem ipsum dolor sit amet, consectetuer adipiscing elit, sed diam nonummy nibh euismod tincidunt ut laoreet dolore magna aliquam erat volutpat. Ut wisi enim ad minim veniam, quis nostrud exerci tation ullamcorper suscipit lobortis nisl ut aliquip ex ea commodo consequat. Duis autem vel eum iriure dolor in hendiusto odio dignissim qui blandit praesent luptatum zzril delenit augue duis dolore te feugait nulla facilisi.</p>
      <p>Lorem ipsum dolor sit amet, consectetuer adipiscing elit, sed diam nonummy nibh euismod tincidunt ut laoreet dolore magna aliquam erat volutpat. Ut wisi enim ad minim veniam, quis nostrud exerci tation ullamcorper suscipit lobortis nisl ut aliquip ex ea commodo consequat. Duis autem vel eum iriure dolor in hendiusto odio dignissim qui blandit praesent luptatum zzril delenit augue duis dolore te feugait nulla facilisi.</p>
      <p>Lorem ipsum dolor sit amet, consectetuer adipiscing elit, sed diam nonummy nibh euismod tincidunt ut laoreet dolore magna aliquam erat volutpat. Ut wisi enim ad minim veniam, quis nostrud exerci tation ullamcorper suscipit lobortis nisl ut aliquip ex ea commodo consequat. Duis autem vel eum iriure dolor in hendiusto odio dignissim qui blandit praesent luptatum zzril delenit augue duis dolore te feugait nulla facilisi.</p>
    </div>
    <p class="closing">Sincerely Your,</p>
    <p class="signature">Your Name</p>
  </section>

  <svg class="footer-wave" viewBox="0 0 908 170" preserveAspectRatio="none" aria-hidden="true">
    <path d="M0 25 Q454 185 908 14 L908 170 L0 170 Z" fill="var(--navy)"/>
    <path d="M0 4 Q454 166 908 8 L908 14 Q454 185 0 25 Z" fill="var(--red)"/>
  </svg>

  <footer class="footer-contact">
    <div class="contact-line">
      <span class="contact-item">
        <svg class="contact-icon" viewBox="0 0 12 12"><path d="M6 0a4 4 0 0 0-4 4c0 3 4 8 4 8s4-5 4-8a4 4 0 0 0-4-4zm0 5.5A1.5 1.5 0 1 1 6 2.5a1.5 1.5 0 0 1 0 3z"/></svg>
        448 Willowmere Ave, Ste 210, Folsom, CA 95999
      </span>
    </div>
    <div class="contact-line">
      <span class="contact-item">
        <svg class="contact-icon" viewBox="0 0 12 12"><path d="M2.5 0.5l2 2.5-1.2 1.4a7 7 0 0 0 4.3 4.3L9 7.5l2.5 2-1.2 2A9.5 9.5 0 0 1 0.5 1.7z"/></svg>
        916-555-0187
      </span>
      <span class="contact-item">
        <svg class="contact-icon" viewBox="0 0 12 12"><path d="M0 2h12v8H0zM1 3v.4l5 3.2 5-3.2V3z"/></svg>
        info@brightfieldventures.example
      </span>
      <span class="contact-item">
        <svg class="contact-icon" viewBox="0 0 12 12"><path d="M6 0a6 6 0 1 0 0 12A6 6 0 0 0 6 0zm0 1c.8 0 1.6 1.6 1.8 4.5H4.2C4.4 2.6 5.2 1 6 1zM1 6.5h2.2c.1 1.6.4 3 .9 3.9A5 5 0 0 1 1 6.5zm0-1a5 5 0 0 1 3.1-3.9c-.5.9-.8 2.3-.9 3.9zm5 5.5c-.8 0-1.6-1.6-1.8-4.5h3.6C7.6 9.4 6.8 11 6 11zm1.9-.6c.5-.9.8-2.3.9-3.9H11a5 5 0 0 1-3.1 3.9zM8.8 5.5c-.1-1.6-.4-3-.9-3.9A5 5 0 0 1 11 5.5z"/></svg>
        brightfieldventures.example
      </span>
    </div>
  </footer>
</main>
</body>
</html>
```